1 Banner für Affiliate-Marketing (Börse/Trading)
Zielgruppe
Wir vermitteln Kunden an einen Broker. Die Kunden eröffnen Handelskonten, in denen sie selbständig Finanzprodukte (CFDs, Forex, Aktien, Edelmetalle,...) gehebelt handeln. Wir bieten dem Kunden eine Dienstleistung an, indem wir Broker vorauswählen, technischen Support liefern, bei der Kontoeröffnung unterstützen und auf Wunsch auch Trader ausbilden.
Zielgruppe: männlich, finanz- und risikoaffin, Spekulant
Aufgabenstellung
Wir benötigen 1 klickstarken Banner für das Affiliate-Marketing
Bannergröße: 300*250
Formate: GIF, PNG, JPG, Vektor
Gerne auch animierte Vorschläge, aber bitte nicht ausschließlich.
Zusätzliche Info, die verarbeitet werden kann (aber nicht muss): Kelvora Bank hat in 2016 bei 2 Kundenumfragen den Testsieg als bester Broker gewonnen.
Design ist frei und muss sich nicht an der Homepage orientieren - vielmehr suchen wir klickstarke Banner aus der Finanz-/Börsenwelt mit Bildern Ihrer Wahl.

```html
<!DOCTYPE html>
<html lang="de">
<head>
<meta charset="utf-8">
<title>Kelvora Bank – Bannerformate</title>
<link rel="stylesheet" href="https://fonts.googleapis.com/css2?family=Open+Sans:wght@700;800&display=swap">
<style>
:root{
  --sheet:#232323;
  --label:#f0f0f0;
  --yellow:#ffd500;
  --navy:#0b1a4d;
  --navy-deep:#07123a;
  --navy-light:#15296b;
  --ink:#262626;
  --rule:rgba(255,255,255,.75);
  --person-a:#7d93b4;
  --person-b:#3e5679;
  --coin-a:#5fe3e6;
  --coin-b:#0a8ea6;
}
*{box-sizing:border-box;margin:0;padding:0}
html,body{width:1200px;height:857px;overflow:hidden;background:var(--sheet)}
body{font-family:"Open Sans",Arial,sans-serif}
.sheet{position:absolute;left:0;top:0;width:1400px;height:1000px;transform:scale(.857143);transform-origin:0 0}

.size-label{position:absolute;color:var(--label);font-weight:700;font-size:17px;letter-spacing:.04em;word-spacing:.3em}

.banner{position:absolute;overflow:hidden;background:linear-gradient(135deg,var(--navy-light) 0%,var(--navy) 45%,var(--navy-deep) 100%)}
.banner > *{position:absolute}
.accent{left:0;top:0;width:100%;height:100%}
.accent polygon{fill:var(--yellow)}

.brand{color:var(--ink);font-weight:800;line-height:1;white-space:nowrap}
.brand-main{display:block;font-size:1em;letter-spacing:.01em}
.brand-sub{display:block;font-size:.46em;letter-spacing:.62em;margin-top:.25em}

.person{background:linear-gradient(180deg,var(--person-a) 0%,var(--person-b) 100%);border-radius:40% 40% 0 0 / 18% 18% 0 0}
.currency{background:linear-gradient(180deg,var(--coin-a),var(--coin-b));border-radius:6px}

.claim-intro,.claim-main{width:19.8em;text-align:center;color:#fff;font-weight:800;white-space:nowrap}
.claim-intro{border-top:1px solid var(--rule);border-bottom:1px solid var(--rule);padding:1.1em 0 1em;line-height:1.12}
.claim-intro span{display:block}
.hat-in{font-size:1.3em}
.year{font-size:3.4em;color:var(--yellow);line-height:1}
.kunden{font-size:1.8em;color:var(--yellow)}
.testsieg{font-size:1.5em}
.claim-main span{display:block}
.bester{font-size:5.4em;line-height:.98;letter-spacing:-.01em}
.broker{font-size:2.7em;line-height:1.3;background:var(--yellow);color:var(--navy);letter-spacing:.34em;padding-left:.34em;margin:.12em 0 .1em;overflow:hidden}
.gewonnen{font-size:3em;line-height:1.15}

.cta{background:var(--yellow);color:var(--navy-deep);font-weight:800;border-radius:5px;display:flex;align-items:center;justify-content:center;box-shadow:0 2px 0 rgba(0,0,0,.35);white-space:nowrap}
</style>
</head>
<body>
<main class="sheet">

  <!-- Leaderboard 728 x 90 -->
  <p class="size-label" style="left:68px;top:103px">728 X 90</p>
  <section class="banner banner-leaderboard" style="left:67px;top:142px;width:728px;height:90px">
    <svg class="accent" viewBox="0 0 728 90" preserveAspectRatio="none" aria-hidden="true"><polygon points="0,0 125,0 142,90 0,90"/></svg>
    <div class="brand" style="left:11px;top:24px;font-size:25px"><span class="brand-main">KELVORA</span><span class="brand-sub">BANK</span></div>
    <div class="claim-intro" style="left:156px;top:7px;font-size:6.7px"><span class="hat-in">HAT IN</span><span class="year">2016 BEI 2</span><span class="kunden">KUNDENUMFRAGEN</span><span class="testsieg">DEN TESTSIEG ALS</span></div>
    <div class="claim-main" style="left:325px;top:5px;font-size:6.2px"><span class="bester">BESTER</span><span class="broker">BROKER</span><span class="gewonnen">GEWONNEN</span></div>
    <div class="person" role="img" aria-label="Foto: junger Mann mit Brille im blauen Hemd" style="left:478px;top:0;width:120px;height:90px"></div>
    <div class="currency" role="img" aria-label="Währungssymbole Yen, Euro, Dollar, Pfund, Franken" style="left:608px;top:13px;width:110px;height:25px"></div>
    <a class="cta" style="left:602px;top:48px;width:119px;height:30px;font-size:13px">HIER KLICKEN</a>
  </section>

  <!-- Banner 468 x 60 -->
  <p class="size-label" style="left:822px;top:103px">468 X 60</p>
  <section class="banner banner-full" style="left:819px;top:142px;width:468px;height:60px">
    <svg class="accent" viewBox="0 0 468 60" preserveAspectRatio="none" aria-hidden="true"><polygon points="0,0 99,0 106,60 0,60"/></svg>
    <div class="brand" style="left:4px;top:9px;font-size:20px"><span class="brand-main">KELVORA</span><span class="brand-sub">BANK</span></div>
    <div class="claim-intro" style="left:112px;top:3px;font-size:4.8px"><span class="hat-in">HAT IN</span><span class="year">2016 BEI 2</span><span class="kunden">KUNDENUMFRAGEN</span><span class="testsieg">DEN TESTSIEG ALS</span></div>
    <div class="claim-main" style="left:222px;top:2px;font-size:4.4px"><span class="bester">BESTER</span><span class="broker">BROKER</span><span class="gewonnen">GEWONNEN</span></div>
    <div class="person" role="img" aria-label="Foto: junger Mann mit Brille im blauen Hemd" style="left:318px;top:0;width:44px;height:60px"></div>
    <a class="cta" style="left:370px;top:16px;width:95px;height:26px;font-size:11px">HIER KLICKEN</a>
  </section>

  <!-- Skyscraper 120 x 600 -->
  <p class="size-label" style="left:66px;top:896px">120 X 600</p>
  <section class="banner banner-skyscraper" style="left:67px;top:284px;width:120px;height:600px">
    <svg class="accent" viewBox="0 0 120 600" preserveAspectRatio="none" aria-hidden="true"><polygon points="0,0 120,0 120,55 0,118"/><polygon points="0,372 120,540 0,600"/></svg>
    <div class="brand" style="left:8px;top:11px;font-size:22px"><span class="brand-main">KELVORA</span><span class="brand-sub">BANK</span></div>
    <div class="claim-intro" style="left:3px;top:160px;font-size:5.7px"><span class="hat-in">HAT IN</span><span class="year">2016 BEI 2</span><span class="kunden">KUNDENUMFRAGEN</span><span class="testsieg">DEN TESTSIEG ALS</span></div>
    <div class="claim-main" style="left:3px;top:250px;font-size:5.7px"><span class="bester">BESTER</span><span class="broker">BROKER</span><span class="gewonnen">GEWONNEN</span></div>
    <div class="currency" role="img" aria-label="Währungssymbole Yen, Euro, Dollar, Pfund, Franken" style="left:10px;top:333px;width:98px;height:24px"></div>
    <div class="person" role="img" aria-label="Foto: junger Mann mit Brille im blauen Hemd" style="left:0;top:368px;width:120px;height:200px"></div>
    <a class="cta" style="left:3px;top:558px;width:114px;height:28px;font-size:12px">HIER KLICKEN</a>
  </section>

  <!-- Wide skyscraper 160 x 600 -->
  <p class="size-label" style="left:237px;top:896px">160 X 600</p>
  <section class="banner banner-wide-skyscraper" style="left:234px;top:284px;width:160px;height:600px">
    <svg class="accent" viewBox="0 0 160 600" preserveAspectRatio="none" aria-hidden="true"><polygon points="0,0 160,0 160,62 0,141"/><polygon points="0,350 160,510 0,600"/></svg>
    <div class="brand" style="left:14px;top:16px;font-size:27px"><span class="brand-main">KELVORA</span><span class="brand-sub">BANK</span></div>
    <div class="claim-intro" style="left:8px;top:176px;font-size:7.2px"><span class="hat-in">HAT IN</span><span class="year">2016 BEI 2</span><span class="kunden">KUNDENUMFRAGEN</span><span class="testsieg">DEN TESTSIEG ALS</span></div>
    <div class="claim-main" style="left:8px;top:258px;font-size:7.2px"><span class="bester">BESTER</span><span class="broker">BROKER</span><span class="gewonnen">GEWONNEN</span></div>
    <div class="person" role="img" aria-label="Foto: junger Mann mit Brille im blauen Hemd, Währungssymbole auf der Hand" style="left:0;top:395px;width:100px;height:205px"></div>
    <div class="currency" role="img" aria-label="Währungssymbole Yen, Euro, Dollar, Pfund, Franken" style="left:60px;top:480px;width:98px;height:25px"></div>
    <a class="cta" style="left:13px;top:560px;width:133px;height:32px;font-size:14px">HIER KLICKEN</a>
  </section>

  <!-- Square 500 x 500 -->
  <p class="size-label" style="left:442px;top:808px">500 X 500</p>
  <section class="banner banner-square" style="left:440px;top:284px;width:500px;height:500px">
    <svg class="accent" viewBox="0 0 500 500" preserveAspectRatio="none" aria-hidden="true"><polygon points="0,0 172,0 285,500 0,500"/></svg>
    <div class="brand" style="left:14px;top:14px;font-size:35px"><span class="brand-main">KELVORA</span><span class="brand-sub">BANK</span></div>
    <div class="person" role="img" aria-label="Foto: lächelnder junger Mann mit Brille im blauen Hemd, Währungssymbole auf der ausgestreckten Hand" style="left:0;top:90px;width:262px;height:410px"></div>
    <div class="claim-intro" style="left:270px;top:26px;font-size:10px"><span class="hat-in">HAT IN</span><span class="year">2016 BEI 2</span><span class="kunden">KUNDENUMFRAGEN</span><span class="testsieg">DEN TESTSIEG ALS</span></div>
    <div class="claim-main" style="left:270px;top:140px;font-size:10px"><span class="bester">BESTER</span><span class="broker">BROKER</span><span class="gewonnen">GEWONNEN</span></div>
    <div class="currency" role="img" aria-label="Währungssymbole Yen, Euro, Dollar, Pfund, Franken" style="left:275px;top:286px;width:193px;height:46px;border-radius:9px"></div>
    <a class="cta" style="left:280px;top:434px;width:202px;height:50px;font-size:22px;border-radius:7px">HIER KLICKEN</a>
  </section>

  <!-- Medium rectangle 300 x 250 -->
  <p class="size-label" style="left:986px;top:551px">300 X 250</p>
  <section class="banner banner-rectangle" style="left:987px;top:284px;width:300px;height:250px">
    <svg class="accent" viewBox="0 0 300 250" preserveAspectRatio="none" aria-hidden="true"><polygon points="0,0 112,0 150,250 0,250"/></svg>
    <div class="brand" style="left:5px;top:6px;font-size:22px"><span class="brand-main">KELVORA</span><span class="brand-sub">BANK</span></div>
    <div class="person" role="img" aria-label="Foto: lächelnder junger Mann mit Brille im blauen Hemd, Währungssymbole auf der Hand" style="left:6px;top:55px;width:148px;height:195px"></div>
    <div class="claim-intro" style="left:161px;top:6px;font-size:6px;border-top-color:transparent;border-bottom-color:transparent"><span class="hat-in">HAT IN</span><span class="year">2016 BEI 2</span><span class="kunden">KUNDENUMFRAGEN</span><span class="testsieg">DEN TESTSIEG ALS</span></div>
    <div class="claim-main" style="left:161px;top:78px;font-size:6px"><span class="bester">BESTER</span><span class="broker">BROKER</span><span class="gewonnen">GEWONNEN</span></div>
    <div class="currency" role="img" aria-label="Währungssymbole Yen, Euro, Dollar, Pfund, Franken" style="left:166px;top:161px;width:111px;height:25px"></div>
    <a class="cta" style="left:166px;top:210px;width:117px;height:30px;font-size:13px">HIER KLICKEN</a>
  </section>

</main>
</body>
</html>
```